Bramblewood Card Company Business Cards

We are a trading card store with Glimmorax, sports and other TCG cards, we need a business card design that encompasses a clean cut, modern style with a retro flare. website is bramblewoodcardco.com for reference. Can utilize a comic book era feel or a more modern outdoor feel to utilize the "Pacific Northwest" elements of tress, mountains, etc.

Industry/Entity Type

Trading cards and collectibles

Contact Information for Business Card

business name, email address, phone number, name, owner job title

Font styles to use
Sans Serif

```html
<!DOCTYPE html>
<html lang="en">
<head>
<meta charset="utf-8">
<title>Bramblewood Card Company – Business Cards</title>
<link rel="stylesheet" href="https://fonts.googleapis.com/css2?family=Arimo:wght@400;700&family=Montserrat:wght@800&display=swap">
<style>
  :root {
    --page: #e6e7e9;
    --card-dark: #2f2f30;
    --card-light: #ffffff;
    --slate: #6f6f70;
    --slate-light: #8a8a8b;
    --cyan: #1fb8e0;
    --ink: #3b3b3c;
    --rule: #c9c9ca;
  }
  * { box-sizing: border-box; margin: 0; padding: 0; }
  html, body { width: 1200px; height: 874px; overflow: hidden; }
  body {
    background: var(--page);
    font-family: "Arimo", Arial, sans-serif;
    position: relative;
  }
  .card {
    position: absolute;
    left: 290px;
    width: 620px;
    height: 354px;
    border-radius: 18px;
    box-shadow: 0 6px 18px rgba(0,0,0,.18);
    overflow: hidden;
  }
  .card--back { top: 62px; background: var(--card-dark); display: flex; align-items: center; justify-content: center; }
  .card--front { top: 458px; background: var(--card-light); }

  .brand-name {
    font-family: "Montserrat", Arial, sans-serif;
    font-weight: 800;
    text-transform: uppercase;
    text-align: center;
    line-height: 1.15;
    letter-spacing: .04em;
  }
  .card--back .brand-name { color: var(--slate); font-size: 34px; }

  .card--front .brand-name {
    position: absolute;
    left: 34px; top: 122px;
    width: 226px;
    color: var(--slate);
    font-size: 21px;
  }
  .divider {
    position: absolute;
    left: 282px; top: 80px;
    width: 2px; height: 190px;
    background: var(--rule);
  }
  .contact {
    position: absolute;
    left: 310px; top: 102px;
    width: 290px;
  }
  .contact__name { color: var(--cyan); font-size: 30px; font-weight: 700; line-height: 1.1; }
  .contact__title { color: var(--slate-light); font-size: 17px; margin-top: 4px; }
  .contact__list { list-style: none; margin-top: 30px; }
  .contact__item {
    display: flex; align-items: center; gap: 9px;
    color: var(--ink); font-size: 17px; line-height: 26px;
    white-space: nowrap;
  }
  .contact__item svg { width: 14px; height: 14px; flex: none; fill: var(--cyan); }
</style>
</head>
<body>
  <section class="card card--back" aria-label="Card back">
    <p class="brand-name">Bramblewood<br>Card Company</p>
  </section>

  <section class="card card--front" aria-label="Card front">
    <p class="brand-name">Bramblewood<br>Card Company</p>
    <div class="divider"></div>
    <div class="contact">
      <h1 class="contact__name">Owen Mercer</h1>
      <p class="contact__title">President</p>
      <ul class="contact__list">
        <li class="contact__item">
          <svg viewBox="0 0 16 16" aria-hidden="true"><path d="M3.5 1l2.5 3-1.5 2c1 2 3 4 5 5l2-1.5 3 2.5-1.5 2.5C8 15 1 8 1 2.5z"/></svg>
          555-014-2290
        </li>
        <li class="contact__item">
          <svg viewBox="0 0 16 16" aria-hidden="true"><path d="M1 3h14v10H1z M2 4l6 5 6-5" fill="none" stroke="#1fb8e0" stroke-width="1.6"/></svg>
          info@bramblewoodcardco.com
        </li>
        <li class="contact__item">
          <svg viewBox="0 0 16 16" aria-hidden="true"><circle cx="8" cy="8" r="7"/></svg>
          www.bramblewoodcardco.com
        </li>
      </ul>
    </div>
  </section>
</body>
</html>
```